Medical centre needs a business card

We are a medcial centre in Australia, needing a new business card. Our demographic is low working class families. We are going to be renovating our premises to modernise the look and also had a new logo done a few months ago representing quality and community, and now need to update our cards. It needs to be doubled sided, with logo and contact details on the front, and appointment details on the back. . Needs to be modern and simple, easy to read. <br/><br/>Name: Kindle Grove Medical Centre <br/>Address: 512 Parmley Rd (Cnr Parmley Rd & Osgood Creek Rd),<br/>Tindarra Court Shopping Centre, Paralowie, SA 5108<br/>Ph: 08 8461 3072<br/>Tag line: Where your wellbeing comes first<br/>Website: www.kindlegrovemedicalcentre-example.com.au<br/>Online bookings also available<br/><br/>(On the back, to have 3 lines of appointments that can be written in.<br/>Day, date, time)<br/><br/>Your next appointment is on<br/>Can try “M T W Th F Sa Su _________________ at ____________ am/pm” or other combinations <br/>Please advise as soon as possible if unable to attend<br/>Cancellation fees apply if less than 2 hrs notice<br/>Online appointments available (please highlight this option by either by position, colour or font)

Target Market(s)

Lower social economic working class, young families to seniors

Industry/Entity Type

Medical Centre

Contact Information for Business Card

Kindle Grove Medical Centre
512 Parmley Rd (Cnr Parmley Rd & Osgood Creek Drive)
Tindarra Court Shopping Centre
Marlowe Heights SA 5190
Ph: 08 8461 3072
www.kindlegrovemedicalcentre-example.com.au
Tagline line: where your wellbeing comes first
Back side is for appointments
Your next appointment is with Dr ______________
Day/date/time (Please give 3 lines of appointments)
Please advise as soon as possible if unable to attend
Cancellation fees apply if less than 2 hours notice
Online appointments available
Book online easily and conveniently (please highlight online appointments)

Font styles to use
Serif
Sans Serif

Colors

Designer to choose colors to be used in the design.

Requirements
Must have
• Modern and simple
• Easy to ready
• Induces a wellbeing feeling
• Incorporate our logo colours and feel from logo
• Induces feeling of stability and security
Nice to have
• Attract attention
• Pleasant to look at
• Feeling of innovation
Should not have
• Loud clashing colours
• Overly luxurious feeling
• Overly artistic

```html
<!DOCTYPE html>
<html lang="en">
<head>
<meta charset="utf-8">
<title>Kindle Grove Medical Centre – Business Card</title>
<link rel="stylesheet" href="https://fonts.googleapis.com/css2?family=Roboto:wght@400;500;700&display=swap">
<style>
  :root {
    --page-bg: #f1ece4;
    --card-bg: #e4e4e2;
    --brand-blue: #1a82c8;
    --text-blue: #2b6fc2;
    --ring-blue: #3a5fb0;
    --rule-grey: #9b918a;
    --accent-green: #8cc63f;
    --white: #ffffff;
  }
  * { box-sizing: border-box; margin: 0; padding: 0; }
  html, body { width: 1200px; height: 844px; overflow: hidden; }
  body {
    background: var(--page-bg);
    font-family: "Roboto", Arial, sans-serif;
    color: var(--text-blue);
    position: relative;
  }
  .card {
    position: absolute;
    width: 560px;
    height: 320px;
    background: var(--card-bg);
    box-shadow: 0 2px 6px rgba(0,0,0,0.12);
  }
  .card--appointment { left: 40px; top: 80px; }
  .card--contact { left: 600px; top: 444px; }

  .brand {
    position: absolute;
    left: 0; right: 0;
    display: flex;
    align-items: center;
    justify-content: center;
    gap: 10px;
  }
  .brand__dot {
    width: 16px; height: 16px;
    border-radius: 50%;
    background: var(--accent-green);
    flex: none;
  }
  .brand__name {
    font-weight: 700;
    font-size: 22px;
    line-height: 1.1;
    color: var(--brand-blue);
    text-align: center;
    text-transform: uppercase;
    letter-spacing: 0.5px;
  }
  .card--appointment .brand { top: 44px; }
  .card--contact .brand { top: 22px; }

  .band {
    position: absolute;
    left: 0; right: 0;
    top: 240px;
    height: 40px;
    background: var(--brand-blue);
    color: var(--white);
    font-size: 18px;
    font-weight: 500;
    display: flex;
    align-items: center;
    justify-content: center;
  }

  /* appointment side */
  .field {
    position: absolute;
    display: flex;
    align-items: flex-end;
    font-size: 16px;
    gap: 6px;
  }
  .field__rule {
    border-bottom: 1px solid var(--rule-grey);
    height: 1px;
    margin-bottom: 4px;
  }
  .field--doctor { left: 36px; top: 124px; }
  .field--doctor .field__rule { width: 240px; }
  .field--date { left: 36px; top: 204px; }
  .field--date .field__rule { width: 190px; }
  .field--time { left: 300px; top: 204px; }
  .field--time .field__rule { width: 70px; }

  .days {
    position: absolute;
    left: 60px; top: 164px;
    display: flex;
    gap: 18px;
    list-style: none;
    font-size: 16px;
  }
  .option { display: flex; align-items: center; gap: 6px; }
  .option__ring {
    width: 15px; height: 15px;
    border: 1.5px solid var(--ring-blue);
    border-radius: 50%;
    flex: none;
  }
  .meridiem { display: flex; align-items: center; gap: 6px; margin-left: 10px; }

  /* contact side */
  .contact {
    position: absolute;
    left: 0; right: 0; top: 78px;
    display: flex;
    flex-direction: column;
    align-items: center;
    font-size: 12px;
    line-height: 1.25;
    text-align: center;
  }
  .contact__icon {
    width: 16px; height: 16px;
    border-radius: 50%;
    background: var(--brand-blue);
    display: flex; align-items: center; justify-content: center;
    margin: 2px 0 2px;
  }
  .contact__icon svg { width: 10px; height: 10px; }
  .contact__block { margin-bottom: 4px; font-style: normal; }
</style>
</head>
<body>

<section class="card card--appointment" aria-label="Appointment side">
  <div class="brand">
    <span class="brand__dot"></span>
    <span class="brand__name">Kindle Grove<br>Medical Centre</span>
  </div>

  <div class="field field--doctor">
    <span>Your next appointment is with Dr</span>
    <span class="field__rule"></span>
  </div>

  <ul class="days">
    <li class="option"><span class="option__ring"></span>Mon</li>
    <li class="option"><span class="option__ring"></span>Tue</li>
    <li class="option"><span class="option__ring"></span>Wed</li>
    <li class="option"><span class="option__ring"></span>Thur</li>
    <li class="option"><span class="option__ring"></span>Fri</li>
    <li class="option"><span class="option__ring"></span>Sat</li>
  </ul>

  <div class="field field--date">
    <span>Date:</span>
    <span class="field__rule"></span>
  </div>
  <div class="field field--time">
    <span>Time:</span>
    <span class="field__rule"></span>
    <span class="meridiem">
      <span class="option"><span class="option__ring"></span>am /</span>
      <span class="option"><span class="option__ring"></span>pm</span>
    </span>
  </div>

  <div class="band">Book online easily and conveniently</div>
</section>

<section class="card card--contact" aria-label="Contact side">
  <div class="brand">
    <span class="brand__dot"></span>
    <span class="brand__name">Kindle Grove<br>Medical Centre</span>
  </div>

  <div class="contact">
    <span class="contact__icon">
      <svg viewBox="0 0 12 12"><path d="M6 0.5a3.8 3.8 0 0 0-3.8 3.8C2.2 7.2 6 11.5 6 11.5s3.8-4.3 3.8-7.2A3.8 3.8 0 0 0 6 0.5z" fill="#fff"/><circle cx="6" cy="4.3" r="1.4" fill="#1a82c8"/></svg>
    </span>
    <address class="contact__block">
      512 Parmley Rd (Cnr Parmley Rd &amp; Osgood Creek Drive)<br>
      Tindarra Court Shopping Centre<br>
      Marlowe Heights SA 5190
    </address>
    <span class="contact__icon">
      <svg viewBox="0 0 12 12"><path d="M2.5 1h2l1 2.6-1.3 1a6 6 0 0 0 3.2 3.2l1-1.3 2.6 1v2c0 .6-.5 1-1 1A9.5 9.5 0 0 1 1.5 2c0-.5.4-1 1-1z" fill="#fff"/></svg>
    </span>
    <span class="contact__block">08 8461 3072</span>
    <span class="contact__icon">
      <svg viewBox="0 0 12 12" fill="none" stroke="#fff" stroke-width="1"><circle cx="6" cy="6" r="5"/><ellipse cx="6" cy="6" rx="2.2" ry="5"/><path d="M1 6h10M1.8 3.5h8.4M1.8 8.5h8.4"/></svg>
    </span>
    <span class="contact__block">www.kindlegrovemedicalcentre-example.com.au</span>
  </div>

  <div class="band">Where your wellbeing comes first</div>
</section>

</body>
</html>
```